Company brochure for our unique consulting business

We are a small consulting business offering a unique set of services to our clients.. In simple terms we are a business improvement consultancy helping our clients get the best out of their businesses. We work with clients across multiple sectors and deliver a variety of services. We want to put together a brochure to cover these main themes:1. Who we are2. What we do3. The type of people we employ4. The sectors we work inWhile the brochure needs to have a certain corporate feel to it, we don't want it to be "boring" or "stiff". We would like it to have a slightly "friendly" or "informal" feel to it, to reflect the type of organisation we are.We have a company website http://brevalconsultingpartners.net , however we do not want to directly replicate the content or feel as we recognise it needs updating.We would like the brochure to be A4 portrait format. We anticipate requiring 12 sides (including covers) but we are happy to be guided on this based on the content we have provided.The attached ppt file gives the detail of the content to be included and also shows the proposed pagination. For the front cover we would like to try 2 versions, one with the BCP logo and one with the Breval Consulting Partners logo (a file of both is attached)One of the most important pages will be the "Our Services" page. We would like this to cover the centre fold. In the ppt file we have shown an example layout, but this is where we need most help - we are clearly not graphic designers! This page will be the most used page in sales meetings etc.Also attached is the following:1. file for our BrevalConsulting Partners company logo.2. File for our BCP company logo3. Files for Derek's signatures (for under photos) - Owen's to follow4. Photo of Derek & Owen (person in purple shirt to be cropped out)Thank you and really excited to see what everyone comes back with.Derek & Owen

Target Market(s)

Very broad - Manufacturing, Healthcare, Hospitality

Industry/Entity Type

Management Consulting

Font styles to use
Other font styles liked:
• We use Swiss721, but happy to be guided by designer

Colors
3276b5
85abd2
0355a3
333333
5c5c5c
9d9d9d
d9d9d9

Requirements
Must have
• Corporate feel
Nice to have
• Slightly friendly feel
• Our standard "blue" is (CORRECTION) - R55 G96 B146 #376092 and our standard grey is R197 G178, B179 - #B3B2B2, which we would like to keep, but other colours we are happy to be guided on. Brand guidelines attached.

```html
<!DOCTYPE html>
<html lang="en">
<head>
<meta charset="utf-8">
<title>BCP — Our Sectors</title>
<link href="https://fonts.googleapis.com/css2?family=Archivo:wght@600;800&display=swap" rel="stylesheet">
<style>
  :root {
    --header-blue: #2b55d4;
    --bar-light: #3f7ff2;
    --bar-dark: #12208a;
    --rule-grey: #3d4450;
    --panel-grey: #dcdddd;
    --footer-blue: #2645b6;
    --logo-ink: #1e2a4a;
    --white: #ffffff;
  }
  * { margin: 0; padding: 0; box-sizing: border-box; }
  html, body { width: 848px; height: 1200px; overflow: hidden; background: var(--white); }
  body { font-family: "Archivo", Arial, sans-serif; }
  .page { position: relative; width: 848px; height: 1200px; overflow: hidden; background: var(--white); }

  .page-head { position: absolute; inset: 0 0 auto 0; height: 140px; z-index: 3; }
  .head-shapes { position: absolute; left: 0; top: 0; width: 848px; height: 140px; }
  .brand-name {
    position: absolute; left: 70px; top: 34px;
    font-weight: 800; font-size: 34px; letter-spacing: 1px; color: var(--logo-ink);
  }
  .page-title {
    position: absolute; left: 390px; top: 72px;
    font-weight: 600; font-size: 31px; color: var(--white);
  }

  .city-photo { position: absolute; left: 0; top: 96px; width: 366px; height: 534px; z-index: 2; }

  .sector-list { position: absolute; left: 32px; top: 154px; width: 763px; list-style: none; z-index: 1; }
  .sector {
    position: relative; height: 145px; margin-bottom: 15px; overflow: hidden;
    display: flex; align-items: center; justify-content: flex-end;
  }
  .sector--light { background: var(--bar-light); }
  .sector--dark { background: var(--bar-dark); }
  .sector-photo { position: absolute; left: 0; top: 0; bottom: 0; width: 62%; }
  .photo-health { background: linear-gradient(90deg, #9fb8ee 0%, #dfe8fb 40%, #c4d5f7 62%, rgba(63,127,242,0) 100%); }
  .photo-manufacturing { background: linear-gradient(90deg, #3a55c8 0%, #1f3aa8 22%, #b9cdf6 48%, #4a66cf 70%, rgba(18,32,138,0) 100%); }
  .photo-hospitality { background: linear-gradient(90deg, #3350b8 0%, #5877d6 22%, #eef3fd 45%, #a8c0f4 68%, rgba(63,127,242,0) 100%); }
  .photo-infrastructure { background: linear-gradient(180deg, rgba(255,255,255,0) 55%, rgba(30,50,150,0.55) 100%), linear-gradient(90deg, #aabff0 0%, #93abea 40%, #4a63c8 62%, rgba(18,32,138,0) 100%); }
  .photo-events { background: radial-gradient(ellipse 28% 65% at 38% 70%, #5675d8 0%, rgba(86,117,216,0) 100%), linear-gradient(90deg, #8aa6ee 0%, #c9d8f8 35%, #a6bff4 60%, rgba(63,127,242,0) 100%); }
  .photo-charities { background: linear-gradient(90deg, #6f86dc 0%, #2f47b4 25%, #5a72d2 45%, #2a3fa8 65%, rgba(18,32,138,0) 100%); }
  .sector-name {
    position: relative; width: 380px; text-align: center;
    font-weight: 800; font-size: 32px; letter-spacing: 1px; color: var(--white);
    text-shadow: 2px 2px 4px rgba(0,0,0,0.55);
  }

  .page-foot {
    position: absolute; left: 0; bottom: 0; width: 848px; height: 78px;
    background: linear-gradient(180deg, #2b4cbd 0%, var(--footer-blue) 100%);
  }
  .page-number { position: absolute; left: 50px; top: 28px; font-size: 19px; color: var(--white); }
</style>
</head>
<body>
<main class="page">
  <header class="page-head">
    <svg class="head-shapes" viewBox="0 0 848 140" aria-hidden="true">
      <polygon points="0,0 258,0 340,96 0,96" fill="var(--panel-grey)"/>
      <polygon points="258,0 848,0 848,124 362,124" fill="var(--header-blue)"/>
      <polygon points="362,124 848,124 848,130 366,130" fill="var(--rule-grey)"/>
    </svg>
    <div class="brand-name">BCP</div>
    <h1 class="page-title">Our Sectors</h1>
  </header>

  <svg class="city-photo" viewBox="0 0 366 534" role="img" aria-label="Black and white photo looking up at city skyscrapers">
    <defs>
      <linearGradient id="cityTone" x1="0" y1="0" x2="1" y2="0.6">
        <stop offset="0" stop-color="#b9bcc0"/>
        <stop offset="0.35" stop-color="#e4e5e7"/>
        <stop offset="0.7" stop-color="#8d9095"/>
        <stop offset="1" stop-color="#5c5f64"/>
      </linearGradient>
    </defs>
    <polygon points="0,0 366,0 0,534" fill="url(#cityTone)"/>
  </svg>

  <ul class="sector-list">
    <li class="sector sector--light"><div class="sector-photo photo-health" role="img" aria-label="Stethoscope resting on a medical chart"></div><span class="sector-name">HEALTH &amp; CARE</span></li>
    <li class="sector sector--dark"><div class="sector-photo photo-manufacturing" role="img" aria-label="Close-up of machining drill bits"></div><span class="sector-name">MANUFACTURING</span></li>
    <li class="sector sector--light"><div class="sector-photo photo-hospitality" role="img" aria-label="Hand opening a hotel room door"></div><span class="sector-name">HOSPITALITY</span></li>
    <li class="sector sector--dark"><div class="sector-photo photo-infrastructure" role="img" aria-label="Long road bridge with street lights"></div><span class="sector-name">INFRASTRUCTURE</span></li>
    <li class="sector sector--light"><div class="sector-photo photo-events" role="img" aria-label="City wrapped into a small globe"></div><span class="sector-name">GLOBAL EVENTS</span></li>
    <li class="sector sector--dark"><div class="sector-photo photo-charities" role="img" aria-label="Young child resting head on hand"></div><span class="sector-name">CHARITIES</span></li>
  </ul>

  <footer class="page-foot">
    <span class="page-number">10</span>
  </footer>
</main>
</body>
</html>
```